Local Flower Farm Needs Business Card Design

I need business cards designed for a flower farm based in Eudora, Kansas.
Business Info:
We are a local cut flower farm located in Eudora, Kansas, founded by Corinne Haldwick. What started as a passion for agriculture and search for more joy in daily life has blossomed into a small business dedicated to providing the community with beautiful, fresh, and sustainable flowers. We specialize in local, seasonal blooms, ensuring that every petal reflects the care and dedication we pour into our craft. Our mission is to deliver the highest quality flowers directly to our customers through local farmers markets and to florists who share our commitment to sustainability. Join us in celebrating the beauty of nature, one bloom at a time!
Contact Details:
Corinne Haldwick
Owner
Phone 913-555-0147
Facebook: Rosalind Thorpe Gardens
Instagram: @RosalindThorpeGardens
Website: RosalindThorpeGardens.example
Target Market(s)
Wholesale to Florists and Direct to Consumer via Farmers Market
Industry/Entity Type
Florist, Farm
Contact Information for Business Card
Name, Contact Info, Logo
Look and feel
Each slider illustrates characteristics of the customer's brand and the style your logo design should communicate.

```html
<!DOCTYPE html>
<html lang="en">
<head>
<meta charset="utf-8">
<title>Rosalind Thorpe Gardens – Business Cards</title>
<link rel="stylesheet" href="https://fonts.googleapis.com/css2?family=Playfair+Display:wght@400&family=Roboto:wght@400;700&display=swap">
<style>
  :root {
    --backdrop: #2b2d30;
    --card: #0f3237;
    --card-edge: #0a262a;
    --ink: #ffffff;
    --ink-soft: #b9c7c9;
  }
  * { box-sizing: border-box; margin: 0; padding: 0; }
  html, body { width: 1200px; height: 900px; overflow: hidden; }
  body {
    background: var(--backdrop);
    font-family: "Roboto", Arial, sans-serif;
    display: flex;
    align-items: center;
    justify-content: center;
    gap: 40px;
  }
  .card {
    position: relative;
    width: 540px;
    height: 309px;
    background: var(--card);
    border-radius: 4px;
    box-shadow: 0 2px 0 var(--card-edge), 0 14px 30px rgba(0,0,0,.35);
    color: var(--ink);
  }
  .holder { position: absolute; left: 30px; top: 30px; }
  .holder__name {
    font-weight: 700;
    font-size: 17px;
    letter-spacing: .5px;
    text-transform: uppercase;
  }
  .holder__role { font-size: 11px; color: var(--ink-soft); margin-top: 3px; }
  .contact {
    position: absolute;
    left: 30px;
    bottom: 34px;
    list-style: none;
    font-size: 12px;
    line-height: 19px;
  }
  .contact li { display: flex; align-items: center; gap: 7px; }
  .contact__icon { width: 10px; height: 10px; flex: none; }
  .brand-seal {
    position: absolute;
    width: 190px;
    height: 190px;
    border: 1.5px solid var(--ink);
    border-radius: 50%;
    display: flex;
    align-items: center;
    justify-content: center;
    text-align: center;
    font-family: "Playfair Display", Georgia, serif;
    font-weight: 400;
    font-size: 19px;
    line-height: 1.3;
    letter-spacing: 2px;
    text-transform: uppercase;
    color: var(--ink);
    padding: 20px;
  }
  .card--front .brand-seal { right: 46px; top: 62px; }
  .card--back .brand-seal {
    left: 50%; top: 50%;
    transform: translate(-50%, -50%);
    width: 150px; height: 150px;
    font-size: 15px;
  }
</style>
</head>
<body>
  <section class="card card--front">
    <div class="holder">
      <p class="holder__name">Corinne Haldwick</p>
      <p class="holder__role">Owner</p>
    </div>
    <ul class="contact">
      <li>
        <svg class="contact__icon" viewBox="0 0 10 10" aria-hidden="true"><path d="M2 0.5 L3.6 0.5 L4.2 3 L3 3.8 Q4 6 6.2 7 L7 5.8 L9.5 6.4 L9.5 8 Q9.5 9.5 8 9.5 Q0.5 9 0.5 2 Q0.5 0.5 2 0.5Z" fill="#fff"/></svg>
        (913)555-0147
      </li>
      <li><svg class="contact__icon" viewBox="0 0 10 10" aria-hidden="true"><circle cx="5" cy="5" r="4.5" fill="#fff"/></svg>Rosalind Thorpe Gardens</li>
      <li><svg class="contact__icon" viewBox="0 0 10 10" aria-hidden="true"><circle cx="5" cy="5" r="4.5" fill="#fff"/></svg>@RosalindThorpeGardens</li>
      <li><svg class="contact__icon" viewBox="0 0 10 10" aria-hidden="true"><circle cx="5" cy="5" r="4.5" fill="#fff"/></svg>RosalindThorpeGardens.example</li>
    </ul>
    <div class="brand-seal">Rosalind Thorpe Gardens</div>
  </section>

  <section class="card card--back">
    <div class="brand-seal">Rosalind Thorpe Gardens</div>
  </section>
</body>
</html>
```